"Thornbury Accupuncture" needs a Promotional Card - A6 size

Requirements
Must have
• Bright colours, pictures of happy people, acupuncture-related pictures.

```html
<!DOCTYPE html>
<html lang="en">
<head>
<meta charset="utf-8">
<title>Thornbury Accupuncture – A6 Promotional Card</title>
<link rel="stylesheet" href="https://fonts.googleapis.com/css2?family=Source+Sans+3:wght@400;600;700&display=swap">
<style>
  :root {
    --red: #e43d28;
    --red-dark: #c92e1c;
    --slate: #2f3f47;
    --gold: #f2c46a;
    --gold-deep: #e9a94a;
    --brown-bar: rgba(72, 36, 22, 0.86);
    --ink: #1d1d1d;
    --white: #ffffff;
    --stage: #ececec;
  }
  * { box-sizing: border-box; margin: 0; padding: 0; }
  html, body { width: 1200px; height: 1200px; overflow: hidden; }
  body {
    background: var(--stage);
    font-family: "Source Sans 3", "Helvetica Neue", Arial, sans-serif;
    color: var(--ink);
    position: relative;
  }
  .card {
    position: absolute;
    top: 198px;
    width: 570px;
    height: 804px;
    background: var(--white);
    overflow: hidden;
  }
  .card--front { left: 21px; }
  .card--back { left: 608px; }
  .abs { position: absolute; }

  /* ---------- front ---------- */
  .hero-photo {
    left: 0; top: 0; width: 570px; height: 300px;
    background: linear-gradient(120deg, #6e4a36 0%, #b98466 22%, #e7c4a6 50%, #f1dcca 75%, #f7ece4 100%);
  }
  .lower-photo {
    left: 0; top: 300px; width: 570px; height: 504px;
    background: linear-gradient(180deg, #ffffff 0%, #fbf1ec 45%, #efd3c8 80%, #e8c3b4 100%);
  }
  .hero-wave { left: 0; top: 0; }
  .brand-name {
    left: 330px; top: 86px; width: 230px;
    text-align: center;
    font-weight: 700; font-size: 27px; line-height: 25px;
    color: var(--red);
    text-transform: lowercase;
  }
  .brand-dot {
    left: 432px; top: 48px; width: 26px; height: 26px;
    border-radius: 50%; background: var(--gold);
  }
  .hero-title {
    left: 199px; top: 160px;
    font-size: 36px; font-weight: 400; color: var(--white);
    white-space: nowrap;
  }
  .section-heading {
    display: flex; align-items: center; gap: 14px;
    font-weight: 700; font-size: 20px; letter-spacing: 0.3px;
    text-transform: uppercase; color: var(--ink);
  }
  .section-heading::before {
    content: ""; width: 18px; height: 18px; border-radius: 50%;
    background: var(--gold); flex: none;
  }
  .about-heading { left: 26px; top: 310px; }
  .about-text { left: 48px; top: 350px; width: 215px; font-size: 17px; line-height: 20.8px; }
  .mission-heading { left: 26px; top: 553px; }
  .mission-text { left: 48px; top: 590px; width: 180px; font-size: 17px; line-height: 20.8px; }

  .service-box {
    left: 309px; top: 367px; width: 227px; height: 272px;
    border: 3px solid var(--gold);
    background: linear-gradient(180deg, rgba(255,255,255,0.9) 0%, #fbe3bd 55%, var(--gold-deep) 100%);
  }
  .service-badge { left: 382px; top: 332px; }
  .service-title { left: 336px; top: 424px; font-weight: 700; font-size: 18px; }
  .service-list { left: 336px; top: 452px; list-style: none; font-size: 17px; line-height: 22.6px; }
  .service-list li { display: flex; align-items: center; gap: 8px; }
  .service-note { left: 336px; top: 584px; width: 190px; font-size: 12px; line-height: 16px; }

  .quote-bar {
    left: 0; top: 676px; width: 570px; height: 92px;
    background: var(--brown-bar);
  }
  .quote-icon { left: 34px; top: 698px; }
  .quote-label { left: 96px; top: 696px; color: var(--white); font-size: 18px; line-height: 20px; }
  .quote-label strong { font-weight: 700; }
  .quote-number { left: 96px; top: 714px; color: var(--white); font-weight: 700; font-size: 35px; letter-spacing: 0.5px; }
  .quote-dot { left: 478px; top: 704px; width: 34px; height: 34px; border-radius: 50%; background: var(--gold); }

  /* ---------- back ---------- */
  .top-band { left: 0; top: 0; width: 570px; height: 104px; background: var(--red); }
  .photo-ring {
    width: 180px; height: 180px; border-radius: 50%;
    background: var(--white); padding: 5px; top: 10px;
  }
  .photo-ring > div { width: 100%; height: 100%; border-radius: 50%; }
  .ring-1 { left: 16px; }
  .ring-2 { left: 196px; }
  .ring-3 { left: 376px; }
  .photo-shoulder { background: radial-gradient(circle at 45% 35%, #e9543c 0%, #d9826e 35%, #8a8f99 75%, #5d636d 100%); }
  .photo-treatment { background: linear-gradient(135deg, #c8957a 0%, #eab8a0 45%, #f2c9b7 70%, #e7a792 100%); }
  .photo-hands { background: linear-gradient(160deg, #f4e3de 0%, #efc7bb 45%, #e7a898 80%, #f6ece8 100%); }

  .intro-text { left: 38px; top: 216px; width: 500px; font-size: 14.5px; line-height: 18.4px; }

  .hours-heading { left: 29px; top: 402px; }
  .hours-table { left: 55px; top: 440px; font-size: 17px; line-height: 20.6px; border-collapse: collapse; }
  .hours-table td { padding: 0; }
  .hours-table td:first-child { width: 138px; }

  .promo {
    left: 356px; top: 378px; width: 172px; height: 97px;
    border-radius: 50%; background: var(--red); color: var(--white);
    display: flex; flex-direction: column; align-items: center; justify-content: center;
  }
  .promo-title { font-weight: 700; font-size: 17px; letter-spacing: 0.3px; }
  .promo-sub { font-size: 14px; }

  .location-heading { left: 29px; top: 514px; }
  .address { left: 55px; top: 552px; font-size: 18px; line-height: 23px; }
  .find-heading { left: 317px; top: 514px; }
  .social { left: 363px; top: 550px; display: flex; gap: 2px; }
  .social span { width: 42px; height: 42px; border-radius: 50%; display: block; }
  .social .s1 { background: var(--slate); }
  .social .s2 { background: var(--gold-deep); }
  .social .s3 { background: var(--red); }

  .footer-wave { left: 0; top: 600px; }
  .portrait-ring {
    left: 46px; top: 614px; width: 164px; height: 164px;
    border-radius: 50%; background: var(--white); padding: 4px;
    box-shadow: 0 3px 8px rgba(0,0,0,0.25);
  }
  .portrait {
    width: 100%; height: 100%; border-radius: 50%;
    background: linear-gradient(180deg, #f4f4f4 0%, #e8e2de 55%, #b89a8a 100%);
  }
  .contact { left: 256px; top: 690px; list-style: none; color: var(--white); font-size: 18px; line-height: 30.5px; }
  .contact li { display: flex; align-items: center; gap: 10px; }
</style>
</head>
<body>

<!-- Front side -->
<section class="card card--front">
  <div class="abs hero-photo" role="img" aria-label="Practitioner placing acupuncture needles in a client's shoulder"></div>
  <div class="abs lower-photo" role="img" aria-label="Soft faded photo of acupuncture needles on skin"></div>
  <svg class="abs hero-wave" width="570" height="320" viewBox="0 0 570 320" aria-hidden="true">
    <path d="M0,242 C120,222 250,246 330,270 C420,296 500,292 570,284 L570,320 L0,320 Z" fill="#ffffff"/>
    <path d="M0,262 C100,240 230,244 292,270 C220,255 100,262 0,292 Z" fill="var(--red)"/>
  </svg>

  <div class="abs brand-dot"></div>
  <div class="abs brand-name">Thornbury Accupuncture</div>
  <div class="abs hero-title">Additional Title Here</div>

  <h2 class="abs section-heading about-heading">About Us</h2>
  <p class="abs about-text">Lorem ipsum dolor sit amet, consectetur adipiscing elit. Sed tempus orci turpis, sit amet ultricies tellus aliquet in. Nullam at suscipit nisl, vel interdum est. Vestibulum et placerat ipsum, vitae.</p>

  <h2 class="abs section-heading mission-heading">Our Mission</h2>
  <p class="abs mission-text">Lorem ipsum dolor sit amet, consectetur adipiscing elit.</p>

  <div class="abs service-box"></div>
  <svg class="abs service-badge" width="80" height="80" viewBox="0 0 80 80" aria-hidden="true">
    <circle cx="40" cy="40" r="40" fill="var(--red)"/>
    <line x1="28" y1="14" x2="40" y2="64" stroke="#fff" stroke-width="2"/>
    <line x1="54" y1="24" x2="38" y2="62" stroke="#fff" stroke-width="2"/>
    <circle cx="28" cy="14" r="2.5" fill="#fff"/>
    <circle cx="54" cy="24" r="2.5" fill="#fff"/>
  </svg>
  <h3 class="abs service-title">Acupuncture</h3>
  <ul class="abs service-list">
    <li><svg width="16" height="14" viewBox="0 0 16 14"><path d="M1,7 L6,12 L15,1" fill="none" stroke="var(--red)" stroke-width="2.5"/></svg>Lorem ipsum</li>
    <li><svg width="16" height="14" viewBox="0 0 16 14"><path d="M1,7 L6,12 L15,1" fill="none" stroke="var(--red)" stroke-width="2.5"/></svg>Lorem ipsum</li>
    <li><svg width="16" height="14" viewBox="0 0 16 14"><path d="M1,7 L6,12 L15,1" fill="none" stroke="var(--red)" stroke-width="2.5"/></svg>Lorem ipsum</li>
    <li><svg width="16" height="14" viewBox="0 0 16 14"><path d="M1,7 L6,12 L15,1" fill="none" stroke="var(--red)" stroke-width="2.5"/></svg>Lorem ipsum</li>
    <li><svg width="16" height="14" viewBox="0 0 16 14"><path d="M1,7 L6,12 L15,1" fill="none" stroke="var(--red)" stroke-width="2.5"/></svg>Lorem ipsum</li>
  </ul>
  <p class="abs service-note">Lorem ipsum dolor sit amet, consectetur adipiscing elit.</p>

  <div class="abs quote-bar"></div>
  <svg class="abs quote-icon" width="54" height="54" viewBox="0 0 54 54" aria-hidden="true">
    <path d="M10,4 C6,6 4,12 8,20 C14,32 24,42 36,48 C44,52 50,48 52,44 L44,34 L36,38 C30,34 22,26 18,20 L22,12 Z" fill="#fff"/>
  </svg>
  <p class="abs quote-label"><strong>FREE QUOTE</strong> CALL OR TEXT</p>
  <p class="abs quote-number">888-888-8888</p>
  <div class="abs quote-dot"></div>
</section>

<!-- Back side -->
<section class="card card--back">
  <div class="abs top-band"></div>
  <div class="abs photo-ring ring-1"><div class="photo-shoulder" role="img" aria-label="Shoulder with highlighted area of pain"></div></div>
  <div class="abs photo-ring ring-2"><div class="photo-treatment" role="img" aria-label="Therapist treating a client's back with a scraping tool"></div></div>
  <div class="abs photo-ring ring-3"><div class="photo-hands" role="img" aria-label="Close-up of hands during a massage treatment"></div></div>

  <p class="abs intro-text">Lorem ipsum dolor sit amet, consectetur adipiscing elit. In iaculis rutrum dignissim. Vestibulum facilisis vulputate cursus. Ut vel nulla eu ante euismod fermentum. Nunc consequat in lectus nec pellentesque. Praesent accumsan accumsan nunc, in condimentum eros cursus et. Vivamus ullamcorper imperdiet porta. Proin interdum sed felis eu viverra. Nam a sollicitudin lectus, a iaculis erat. Aenean ut urna auctor eros pulvinar dictum eget vitae lacus. Suspendisse a dapibus lacus. Integer vel fermentum augue, in mollis tortor. Cras sit amet erat.</p>

  <h2 class="abs section-heading hours-heading">Hours</h2>
  <table class="abs hours-table">
    <tr><td>Monday to Friday</td><td>9:00 AM – 7:00 PM</td></tr>
    <tr><td>Saturday</td><td>9:00 AM – 3:00 PM</td></tr>
  </table>

  <div class="abs promo">
    <span class="promo-title">PROMOTION</span>
    <span class="promo-sub">Best Offer Here</span>
  </div>

  <h2 class="abs section-heading location-heading">Location</h2>
  <p class="abs address">Unit, Street, City<br>State, Zip Code</p>

  <h2 class="abs section-heading find-heading">Find Us On</h2>
  <div class="abs social" aria-label="Social media links"><span class="s1"></span><span class="s2"></span><span class="s3"></span></div>

  <svg class="abs footer-wave" width="570" height="204" viewBox="0 0 570 204" aria-hidden="true">
    <path d="M0,62 C150,44 300,22 400,28 C480,33 540,50 570,66 L570,204 L0,204 Z" fill="var(--red)"/>
    <path d="M0,110 C150,92 300,52 420,46 C490,43 540,60 570,78 L570,204 L0,204 Z" fill="#ffffff"/>
    <path d="M0,112 C150,96 300,58 420,52 C490,49 540,66 570,84 L570,204 L0,204 Z" fill="var(--slate)"/>
  </svg>
  <div class="abs portrait-ring"><div class="portrait" role="img" aria-label="Portrait of the practitioner"></div></div>

  <ul class="abs contact">
    <li><svg width="20" height="20" viewBox="0 0 20 20"><path d="M4,2 C2,3 1,6 3,9 C6,14 10,17 14,18 C17,19 18,17 18,16 L15,12 L12,14 C9,12 7,10 6,8 L8,5 Z" fill="none" stroke="#fff" stroke-width="1.5"/></svg>888-888-8888</li>
    <li><svg width="20" height="20" viewBox="0 0 20 20"><rect x="1.5" y="4" width="17" height="12" fill="none" stroke="#fff" stroke-width="1.5"/><path d="M1.5,4 L10,11 L18.5,4" fill="none" stroke="#fff" stroke-width="1.5"/></svg>name@email.com</li>
    <li><svg width="20" height="20" viewBox="0 0 20 20"><path d="M2,10 L10,3 L18,10 M4.5,8 L4.5,17 L8,17 L8,12 L12,12 L12,17 L15.5,17 L15.5,8" fill="none" stroke="#fff" stroke-width="1.5"/></svg>domain.com</li>
  </ul>
</section>

</body>
</html>
```